Webdesign für Software-Unternehmen
Zielgruppe
Wir sind ein Software-Unternehmen, das sich auf die Anpassung des Kestrel-Betriebssystems für industrielle und kommerzielle Anwendungen spezialisiert hat. Unsere Kunden sind Produkt-Hersteller in unterschiedlichen Branchen, die Kestrel in ihren Produkten einsetzen möchten/müssen.
Aufgabenstellung
Die Farben und Schriftarten sollen sich am Corporate Design der restlichen Website orientieren. Idealerweise soll das Design in Skizzo erstellt werden. Das CMS, mit dem das Design umgesetzt wird, ist der Site Core von LeadNest. Bei Verwendung von existierenden Icons bitte ausschließlich die kostenlosen Icons von GlyphVault (solid) nutzen. Eigene (passende) Icons dürfen auch erstellt werden.

```html
<!DOCTYPE html>
<html lang="en">
<head>
<meta charset="utf-8">
<title>Kestrel Plans – quorvix</title>
<link href="https://fonts.googleapis.com/css2?family=Open+Sans:wght@400;500;600;700&display=swap" rel="stylesheet">
<style>
:root{
  --navy:#0c2a4b;
  --blue:#1a8cff;
  --mint:#00f79c;
  --green:#4caf50;
  --grey:#8a8f96;
  --ink:#1b2430;
  --tint:#f2f7fd;
  --soft:#eaf1fa;
  --line:#dde5ee;
  --white:#ffffff;
}
*{box-sizing:border-box;margin:0;padding:0}
html,body{width:1200px;height:4667px;overflow:hidden}
body{font-family:"Open Sans",Arial,sans-serif;color:var(--ink);background:var(--white);position:relative}
.ic{width:18px;height:18px;display:inline-block;vertical-align:middle}
.tick{color:var(--green)} .plus{color:var(--blue)} .cross{color:var(--grey)}

/* hero */
.hero{position:absolute;left:0;top:0;width:1200px;height:1302px;background:var(--navy);color:var(--white)}
.hero-title{position:absolute;top:110px;width:100%;text-align:center;font-size:25px;font-weight:500}
.hero-sub{position:absolute;top:156px;width:100%;text-align:center;font-size:12px;opacity:.9}

.plan{position:absolute;top:218px;width:309px;height:729px;background:var(--white);border-radius:12px;overflow:hidden;color:var(--ink)}
.plan-head{height:130px;text-align:center;color:var(--white);padding-top:38px;background:var(--blue)}
.plan--flex .plan-head{background:var(--mint);color:var(--ink)}
.plan-name{font-size:28px;font-weight:600;line-height:1.1}
.plan-tag{font-size:10px;margin-top:20px;opacity:.95}
.plan-pill{margin:27px auto 0;width:271px;height:33px;background:#eef2f7;border-radius:4px;font-size:14px;font-weight:500;display:flex;align-items:center;justify-content:center;gap:20px}
.plan-note{text-align:center;color:var(--blue);font-size:10px;margin-top:14px}
.features{list-style:none;margin:20px 18px 0}
.features li{height:38px;display:flex;align-items:center;justify-content:space-between;padding:0 12px 0 10px;font-size:12px}
.features li.support{background:var(--soft)}
.features .meta{color:var(--grey);font-size:10px}
.features .icons{display:flex;gap:8px;color:var(--green)}
.plan-price{position:absolute;top:580px;width:100%;text-align:center;font-size:21px;font-weight:700}
.plan-bill{position:absolute;top:614px;width:100%;text-align:center;font-size:11px;color:var(--blue)}
.plan-btn{position:absolute;top:650px;left:72px;width:165px;height:40px;background:var(--blue);color:var(--white);font-size:15px;font-weight:700;display:flex;align-items:center;justify-content:center;clip-path:polygon(0 0,100% 0,100% 72%,91% 100%,0 100%)}

.include-title{position:absolute;top:1038px;width:100%;text-align:center;font-size:20px;font-weight:500}
.include-sub{position:absolute;top:1074px;width:100%;text-align:center;font-size:11px;opacity:.9}
.perk{position:absolute;top:1132px}
.perk-head{display:flex;align-items:center;gap:14px;font-size:19px;font-weight:400}
.perk-mark{width:40px;height:40px;border-radius:50%;background:var(--white)}
.perk-head svg{width:34px;height:34px;color:var(--white)}
.perk p{font-size:11px;opacity:.85;margin-top:10px}

/* compare */
.compare-title{position:absolute;top:1372px;width:100%;text-align:center;font-size:26px;font-weight:600}
.compare-sub{position:absolute;top:1413px;width:100%;text-align:center;font-size:12px}
.tables{position:absolute;top:1461px;left:113px;width:975px}
.table{border:1px solid var(--line);border-radius:10px;overflow:hidden;margin-bottom:27px;display:grid;grid-template-columns:333px 214px 214px 214px}
.table > div{height:58px;display:flex;align-items:center;justify-content:center;border-top:1px solid var(--line)}
.table > .h{border-top:none;color:var(--white);font-size:14px;font-weight:700;text-transform:uppercase;letter-spacing:.3px}
.table > .h.group{background:var(--soft);color:var(--ink);text-transform:none;font-weight:500;font-size:15px;justify-content:flex-start;padding-left:47px;letter-spacing:0}
.h.s,.h.e{background:var(--blue)} .h.f{background:var(--mint);color:var(--ink)}
.table > .lbl{justify-content:flex-start;padding-left:49px;font-size:13px;background:var(--white)}
.table > .c{background:var(--tint)}
.table .ic{width:20px;height:20px}

/* faq */
.faq-title{position:absolute;top:3496px;width:100%;text-align:center;font-size:26px;font-weight:600}
.faq-sub{position:absolute;top:3540px;width:100%;text-align:center;font-size:12px}
.faq-group{position:absolute;left:113px;width:975px}
.faq-group h3{position:absolute;left:32px;font-size:18px;font-weight:600}
.faq-box{position:absolute;left:0;width:975px;background:var(--soft);border-radius:10px}
.faq-box p{position:absolute;left:32px;font-size:15px;font-weight:500}

/* cta */
.cta{position:absolute;left:129px;top:4283px;width:942px;height:281px;background:var(--navy);border-radius:6px;color:var(--white)}
.cta h2{position:absolute;left:76px;top:74px;font-size:32px;font-weight:700}
.cta .line1{position:absolute;left:76px;top:142px;font-size:15px;display:flex;align-items:center;gap:12px}
.cta .line1 svg{width:28px;height:28px;color:var(--green)}
.cta .line2{position:absolute;left:80px;top:182px;font-size:15px}
.cta-brand{position:absolute;left:686px;top:88px;display:flex;align-items:center;gap:10px;font-size:16px;font-weight:600;color:var(--green)}
.cta-brand span.dot{width:40px;height:40px;border-radius:50%;background:var(--green)}
.cta-btn{position:absolute;left:634px;top:139px;width:205px;height:48px;background:var(--blue);font-size:15px;font-weight:600;display:flex;align-items:center;justify-content:center;clip-path:polygon(0 0,100% 0,100% 70%,93% 100%,0 100%)}
</style>
</head>
<body>
<svg width="0" height="0" style="position:absolute">
  <defs>
    <symbol id="tick" viewBox="0 0 20 20"><path d="M4 10.5l4 4 8-9" fill="none" stroke="currentColor" stroke-width="2.4" stroke-linecap="round" stroke-linejoin="round"/></symbol>
    <symbol id="plus" viewBox="0 0 20 20"><path d="M10 3v14M3 10h14" fill="none" stroke="currentColor" stroke-width="2.6" stroke-linecap="round"/></symbol>
    <symbol id="cross" viewBox="0 0 20 20"><path d="M5 5l10 10M15 5L5 15" fill="none" stroke="currentColor" stroke-width="2.6" stroke-linecap="round"/></symbol>
    <symbol id="chat" viewBox="0 0 20 20"><path d="M2 3h16v11H8l-4 4v-4H2z" fill="currentColor"/></symbol>
    <symbol id="mail" viewBox="0 0 20 20"><rect x="2" y="4" width="16" height="12" rx="1.5" fill="currentColor"/><path d="M2.5 5l7.5 6 7.5-6" fill="none" stroke="#fff" stroke-width="1.4"/></symbol>
    <symbol id="phone" viewBox="0 0 20 20"><path d="M5 2l3 4-2 2c1 2.5 3.5 5 6 6l2-2 4 3-2 3C9 18 2 11 2 4z" fill="none" stroke="currentColor" stroke-width="1.8" stroke-linejoin="round"/></symbol>
    <symbol id="chev" viewBox="0 0 20 20"><path d="M6 8l4 4 4-4" fill="none" stroke="currentColor" stroke-width="2.2" stroke-linecap="round"/></symbol>
    <symbol id="headset" viewBox="0 0 32 32"><path d="M6 18v-3a10 10 0 0 1 20 0v3" fill="none" stroke="currentColor" stroke-width="3"/><rect x="4" y="17" width="6" height="9" rx="2" fill="currentColor"/><rect x="22" y="17" width="6" height="9" rx="2" fill="currentColor"/><path d="M25 26c0 3-4 4-8 4" fill="none" stroke="currentColor" stroke-width="2"/></symbol>
    <symbol id="db" viewBox="0 0 32 32"><ellipse cx="16" cy="6" rx="12" ry="4" fill="currentColor"/><path d="M4 9c0 5 24 5 24 0v6c0 5-24 5-24 0zM4 18c0 5 24 5 24 0v7c0 5-24 5-24 0z" fill="currentColor"/></symbol>
  </defs>
</svg>

<section class="hero">
  <h1 class="hero-title">Build your next product with Kestrel</h1>
  <p class="hero-sub">Take care of your connected Kestrel™ devices. Cover all steps of your product lifecycle with quorvix.</p>

  <article class="plan plan--starter" style="left:113px">
    <header class="plan-head"><div class="plan-name">Starter</div><div class="plan-tag">For prototyping and individual projects.</div></header>
    <div class="plan-pill">Max 3 devices</div>
    <p class="plan-note">Free starter plan with no time limit.</p>
    <ul class="features">
      <li>Kestrel OS <span class="meta">Prebuilt</span></li>
      <li>Security updates <svg class="ic tick"><use href="#tick"/></svg></li>
      <li>Limited setup automation <svg class="ic tick"><use href="#tick"/></svg></li>
      <li>Limited device management <svg class="ic tick"><use href="#tick"/></svg></li>
      <li>Limited application storage <svg class="ic tick"><use href="#tick"/></svg></li>
      <li class="support">Support <span class="icons"><svg class="ic"><use href="#chat"/></svg></span></li>
    </ul>
    <div class="plan-price">Free forever</div>
    <div class="plan-bill">No credit card required</div>
    <a class="plan-btn">Start now</a>
  </article>

  <article class="plan plan--flex" style="left:446px">
    <header class="plan-head"><div class="plan-name">Flex</div><div class="plan-tag">For growing projects with specific requirements.</div></header>
    <div class="plan-pill">Select devices <svg class="ic" style="width:14px;height:14px"><use href="#chev"/></svg></div>
    <p class="plan-note">Discount for volume orders.</p>
    <ul class="features">
      <li>Kestrel OS <span class="meta">Prebuilt</span></li>
      <li>Security updates <svg class="ic tick"><use href="#tick"/></svg></li>
      <li>Full setup automation <svg class="ic tick"><use href="#tick"/></svg></li>
      <li>Device management <svg class="ic tick"><use href="#tick"/></svg></li>
      <li>Application storage <svg class="ic tick"><use href="#tick"/></svg></li>
      <li class="support">Support <span class="icons"><svg class="ic"><use href="#chat"/></svg><svg class="ic"><use href="#mail"/></svg></span></li>
    </ul>
    <div class="plan-price">$ 80 / month</div>
    <div class="plan-bill">Billed annually</div>
    <a class="plan-btn">Get Started</a>
  </article>

  <article class="plan plan--enterprise" style="left:780px">
    <header class="plan-head"><div class="plan-name">Enterprise</div><div class="plan-tag">For large and highly customized projects.</div></header>
    <div class="plan-pill">Unlimited devices</div>
    <p class="plan-note">Individual pricing based on requirements.</p>
    <ul class="features">
      <li>Kestrel OS <span class="meta">Custom</span></li>
      <li>Security updates <svg class="ic tick"><use href="#tick"/></svg></li>
      <li>Full setup automation <svg class="ic tick"><use href="#tick"/></svg></li>
      <li>Full Device management <svg class="ic tick"><use href="#tick"/></svg></li>
      <li>Application storage <svg class="ic tick"><use href="#tick"/></svg></li>
      <li class="support">Support <span class="icons"><svg class="ic"><use href="#chat"/></svg><svg class="ic"><use href="#mail"/></svg><svg class="ic"><use href="#phone"/></svg></span></li>
      <li>Custom hardware <svg class="ic tick"><use href="#tick"/></svg></li>
      <li>Extended OS LTS <svg class="ic tick"><use href="#tick"/></svg></li>
    </ul>
    <div class="plan-price">Let's talk</div>
    <div class="plan-bill">Custom pricing</div>
    <a class="plan-btn">Contact Us</a>
  </article>

  <h2 class="include-title">All Plans Include</h2>
  <p class="include-sub">Every plan comes with these essential features</p>
  <div class="perk" style="left:113px">
    <div class="perk-head"><span class="perk-mark"></span>Secure Kestrel OS</div>
    <p>Ensure your devices run on a secure platform.</p>
  </div>
  <div class="perk" style="left:399px">
    <div class="perk-head"><svg><use href="#headset"/></svg>Long-term software support</div>
    <p>Receive updates and support for the long term.</p>
  </div>
  <div class="perk" style="left:729px">
    <div class="perk-head"><svg><use href="#db"/></svg>GDPR compliance + EU data centers</div>
    <p>Your data is handled securely and in compliance with GDPR.</p>
  </div>
</section>

<h2 class="compare-title">Compare Plans</h2>
<p class="compare-sub">Find the perfect plan for you</p>

<div class="tables">
  <div class="table">
    <div class="h group">The Essentials</div><div class="h s">Stater</div><div class="h f">Flex</div><div class="h e">Enterprise</div>
    <div class="lbl">Kestrel OS</div><div class="c"><svg class="ic tick"><use href="#tick"/></svg></div><div class="c"><svg class="ic tick"><use href="#tick"/></svg></div><div class="c"><svg class="ic tick"><use href="#tick"/></svg></div>
    <div class="lbl">Kiosk Mode</div><div class="c"><svg class="ic tick"><use href="#tick"/></svg></div><div class="c"><svg class="ic tick"><use href="#tick"/></svg></div><div class="c"><svg class="ic tick"><use href="#tick"/></svg></div>
    <div class="lbl">Root Access</div><div class="c"><svg class="ic tick"><use href="#tick"/></svg></div><div class="c"><svg class="ic tick"><use href="#tick"/></svg></div><div class="c"><svg class="ic tick"><use href="#tick"/></svg></div>
    <div class="lbl">Setup Automation</div><div class="c"><svg class="ic plus"><use href="#plus"/></svg></div><div class="c"><svg class="ic plus"><use href="#plus"/></svg></div><div class="c"><svg class="ic tick"><use href="#tick"/></svg></div>
    <div class="lbl">Application Storage</div><div class="c"><svg class="ic plus"><use href="#plus"/></svg></div><div class="c"><svg class="ic plus"><use href="#plus"/></svg></div><div class="c"><svg class="ic tick"><use href="#tick"/></svg></div>
  </div>

  <div class="table">
    <div class="h group">Security &amp; Compliance</div><div class="h s">Stater</div><div class="h f">Flex</div><div class="h e">Enterprise</div>
    <div class="lbl">Over-The-Air Software Updates</div><div class="c"><svg class="ic tick"><use href="#tick"/></svg></div><div class="c"><svg class="ic tick"><use href="#tick"/></svg></div><div class="c"><svg class="ic tick"><use href="#tick"/></svg></div>
    <div class="lbl">EU Data Centers</div><div class="c"><svg class="ic tick"><use href="#tick"/></svg></div><div class="c"><svg class="ic tick"><use href="#tick"/></svg></div><div class="c"><svg class="ic tick"><use href="#tick"/></svg></div>
    <div class="lbl">Long-Term Support</div><div class="c"><svg class="ic tick"><use href="#tick"/></svg></div><div class="c"><svg class="ic tick"><use href="#tick"/></svg></div><div class="c"><svg class="ic tick"><use href="#tick"/></svg></div>
    <div class="lbl">Extended Support Period</div><div class="c"><svg class="ic cross"><use href="#cross"/></svg></div><div class="c"><svg class="ic cross"><use href="#cross"/></svg></div><div class="c"><svg class="ic tick"><use href="#tick"/></svg></div>
    <div class="lbl">Custom Signing Certificates</div><div class="c"><svg class="ic cross"><use href="#cross"/></svg></div><div class="c"><svg class="ic cross"><use href="#cross"/></svg></div><div class="c"><svg class="ic tick"><use href="#tick"/></svg></div>
    <div class="lbl">On-Premise OS Builds</div><div class="c"><svg class="ic cross"><use href="#cross"/></svg></div><div class="c"><svg class="ic cross"><use href="#cross"/></svg></div><div class="c"><svg class="ic tick"><use href="#tick"/></svg></div>
  </div>

  <div class="table">
    <div class="h group">Remote Device Management</div><div class="h s">Stater</div><div class="h f">Flex</div><div class="h e">Enterprise</div>
    <div class="lbl">VNC Access</div><div class="c"><svg class="ic tick"><use href="#tick"/></svg></div><div class="c"><svg class="ic tick"><use href="#tick"/></svg></div><div class="c"><svg class="ic tick"><use href="#tick"/></svg></div>
    <div class="lbl">SSH Access</div><div class="c"><svg class="ic tick"><use href="#tick"/></svg></div><div class="c"><svg class="ic tick"><use href="#tick"/></svg></div><div class="c"><svg class="ic tick"><use href="#tick"/></svg></div>
    <div class="lbl">Static IP Configuration</div><div class="c"><svg class="ic tick"><use href="#tick"/></svg></div><div class="c"><svg class="ic tick"><use href="#tick"/></svg></div><div class="c"><svg class="ic tick"><use href="#tick"/></svg></div>
    <div class="lbl">Device Management</div><div class="c"><svg class="ic tick"><use href="#tick"/></svg></div><div class="c"><svg class="ic tick"><use href="#tick"/></svg></div><div class="c"><svg class="ic tick"><use href="#tick"/></svg></div>
    <div class="lbl">Device Monitoring</div><div class="c"><svg class="ic tick"><use href="#tick"/></svg></div><div class="c"><svg class="ic plus"><use href="#plus"/></svg></div><div class="c"><svg class="ic tick"><use href="#tick"/></svg></div>
    <div class="lbl">Group Configuration</div><div class="c"><svg class="ic tick"><use href="#tick"/></svg></div><div class="c"><svg class="ic plus"><use href="#plus"/></svg></div><div class="c"><svg class="ic tick"><use href="#tick"/></svg></div>
    <div class="lbl">Remote App Deployment</div><div class="c"><svg class="ic cross"><use href="#cross"/></svg></div><div class="c"><svg class="ic plus"><use href="#plus"/></svg></div><div class="c"><svg class="ic tick"><use href="#tick"/></svg></div>
    <div class="lbl">On-Premise Management</div><div class="c"><svg class="ic cross"><use href="#cross"/></svg></div><div class="c"><svg class="ic plus"><use href="#plus"/></svg></div><div class="c"><svg class="ic tick"><use href="#tick"/></svg></div>
  </div>

  <div class="table">
    <div class="h group">Support &amp; Services</div><div class="h s">Stater</div><div class="h f">Flex</div><div class="h e">Enterprise</div>
    <div class="lbl">Forum Support</div><div class="c"><svg class="ic tick"><use href="#tick"/></svg></div><div class="c"><svg class="ic tick"><use href="#tick"/></svg></div><div class="c"><svg class="ic tick"><use href="#tick"/></svg></div>
    <div class="lbl">Mail Support</div><div class="c"><svg class="ic cross"><use href="#cross"/></svg></div><div class="c"><svg class="ic tick"><use href="#tick"/></svg></div><div class="c"><svg class="ic tick"><use href="#tick"/></svg></div>
    <div class="lbl">Emergency Hotline</div><div class="c"><svg class="ic cross"><use href="#cross"/></svg></div><div class="c"><svg class="ic cross"><use href="#cross"/></svg></div><div class="c"><svg class="ic tick"><use href="#tick"/></svg></div>
    <div class="lbl">Enterprise SLA</div><div class="c"><svg class="ic cross"><use href="#cross"/></svg></div><div class="c"><svg class="ic cross"><use href="#cross"/></svg></div><div class="c"><svg class="ic tick"><use href="#tick"/></svg></div>
  </div>

  <div class="table">
    <div class="h group">Customization &amp; Branding</div><div class="h s">Stater</div><div class="h f">Flex</div><div class="h e">Enterprise</div>
    <div class="lbl">Custom Kestrel BSP</div><div class="c"><svg class="ic cross"><use href="#cross"/></svg></div><div class="c"><svg class="ic cross"><use href="#cross"/></svg></div><div class="c"><svg class="ic tick"><use href="#tick"/></svg></div>
    <div class="lbl">Custom Device</div><div class="c"><svg class="ic cross"><use href="#cross"/></svg></div><div class="c"><svg class="ic cross"><use href="#cross"/></svg></div><div class="c"><svg class="ic tick"><use href="#tick"/></svg></div>
    <div class="lbl">Tailored Product Branding</div><div class="c"><svg class="ic cross"><use href="#cross"/></svg></div><div class="c"><svg class="ic cross"><use href="#cross"/></svg></div><div class="c"><svg class="ic tick"><use href="#tick"/></svg></div>
    <div class="lbl">Additional Requirements</div><div class="c"><svg class="ic cross"><use href="#cross"/></svg></div><div class="c"><svg class="ic cross"><use href="#cross"/></svg></div><div class="c"><svg class="ic tick"><use href="#tick"/></svg></div>
  </div>
</div>

<h2 class="faq-title">Frequently Asked Questions</h2>
<p class="faq-sub">Find answers to common questions about our plans and services</p>

<div class="faq-group" style="top:3578px">
  <h3 style="top:0">Plans &amp; Pricing</h3>
  <div class="faq-box" style="top:43px;height:189px">
    <p style="top:25px">Does The Free Starter Plan Have A Time Limit? ▼</p>
    <p style="top:83px">My Devices Will Stay Offline Forever. Can I Just Buy A License For The Kestrel OS? ▼</p>
    <p style="top:141px">Why Do I Need To Purchase A Plan To Use An Operating System? ▼</p>
  </div>
</div>
<div class="faq-group" style="top:3843px">
  <h3 style="top:0">Licensing</h3>
  <div class="faq-box" style="top:41px;height:114px">
    <p style="top:21px">If My Kestrel Device Stays Offline, Will It Eventually Switch Back To Evaluation Mode? ▼</p>
    <p style="top:74px">What Happens To My Kestrel OS License If My Device Breaks? ▼</p>
  </div>
</div>
<div class="faq-group" style="top:4031px">
  <h3 style="top:0">Support</h3>
  <div class="faq-box" style="top:43px;height:116px">
    <p style="top:21px">I Have Special Requirements, Do You Provide Custom Kestrel Solutions? ▼</p>
    <p style="top:69px">What Support Options Are Available? ▼</p>
  </div>
</div>

<section class="cta">
  <h2>Got Questions?</h2>
  <div class="line1"><svg><use href="#chat"/></svg>Our Experts Are Here To Help.</div>
  <p class="line2">Contact Us To Get All The Answers You Need!</p>
  <div class="cta-brand"><span class="dot"></span>Kestrel</div>
  <a class="cta-btn">Contact our experts</a>
</section>
</body>
</html>
```